Medical consulting firm needs polished website

I am a physician and working on setting up a smal consulting firm in New Hampshire, USA. It is called Bright Harbor Medical Services, LLC and the website will be BrightHarborMed.com. I was puttering around at making my own website, and it just didn't come together nicely so I've decided to leave it to the pros. The focus of the business is Advanced Care Planning, ie planning for your future medical needs. So it deals with some heavy stuff like planning for if you get sick, who should make decisions for you, end of life options etc. So it can't be too flippant or cutesy, but also can't be too dour and dark. I am hoping to convey that by thinking ahead and making some plans you can lift some of the worries off of yourself and your family - and that we can help make a scary sounding path more manageable. I want it to be made with wordpress and I have actually already bought a template ( Vitarun – A Modern Multidisciplinary Medical & Health Theme ). The website needs to have general information about our services, doc profile, appointment maker, blog/url link page, and ideally web commerce application ( the template has access to woocommerce). I've posted my business card and current brochure (still tweaking them, but you get the idea). I am also partnering with lumenfold.com and so have included their logo and would want connections/info about them. I have the logos etc in different formats as needed.

Target Market(s)

middle aged to older adults

Industry/Entity Type

Medical

Coding

Coded - Design and coding required

Font styles to use
Sans Serif

Requirements
Must have
• as above.
Nice to have
• Ease of reading/access for elderly viewers. woo commerce.

```html
<!DOCTYPE html>
<html lang="en">
<head>
<meta charset="utf-8">
<title>Bright Harbor Medical Services, LLC</title>
<link rel="stylesheet" href="https://fonts.googleapis.com/css2?family=Roboto:wght@400;500&display=swap">
<style>
:root{
  --blue:#2f86d6;
  --blue-light:#6bb5f5;
  --nav-blue:#1f6fc0;
  --green:#3aa832;
  --ink:#222;
  --white:#fff;
  --photo-a:#d9d6d1;
  --photo-b:#c9c3bb;
  --photo-c:#efece8;
}
*{box-sizing:border-box;margin:0;padding:0}
html,body{width:1200px;height:676px;overflow:hidden;background:var(--white);font-family:'Roboto',Arial,sans-serif}
.site{position:relative;width:1200px;height:676px;overflow:hidden}
.topbar{height:36px;background:linear-gradient(90deg,var(--blue),var(--blue-light));display:flex;align-items:center;justify-content:flex-end;gap:26px;padding-right:40px;color:var(--white);font-size:13px}
.topbar-item{display:flex;align-items:center;gap:5px}
.appointment-btn{background:var(--white);color:var(--ink);font-size:13px;padding:3px 7px;border-radius:3px}
.header{height:76px;display:flex;align-items:center;justify-content:space-between;padding:0 48px 0 60px;border-bottom:1px solid #e6e6e6}
.brand{display:flex;align-items:center;gap:12px}
.brand-mark{width:46px;height:46px;border-radius:50%;background:var(--blue)}
.brand-name{font-size:26px;font-weight:400;color:var(--nav-blue)}
.nav{display:flex;gap:34px;list-style:none;font-size:15px;font-weight:500;text-transform:uppercase;color:var(--nav-blue)}
.nav .is-active{color:var(--green)}
.hero-photo{position:absolute;top:112px;left:0;width:1200px;height:436px;background:linear-gradient(110deg,var(--photo-c) 0%,var(--photo-a) 45%,var(--photo-b) 100%)}
.intro{position:absolute;top:470px;left:90px;width:1030px;height:104px;background:linear-gradient(90deg,var(--blue),var(--blue-light));color:var(--white);text-align:center;padding:18px 24px 0}
.intro-title{font-size:17px;font-weight:500;margin-bottom:14px}
.intro-text{font-size:12.5px;line-height:17px}
.services-heading{position:absolute;top:600px;left:0;width:1200px;text-align:center;font-size:21px;font-weight:500;color:var(--ink)}
.services-heading span{color:var(--nav-blue)}
.divider{position:absolute;top:636px;left:100px;width:1000px;border-top:1px dashed var(--blue)}
</style>
</head>
<body>
<div class="site">
  <div class="topbar">
    <span class="topbar-item">
      <svg width="12" height="12" viewBox="0 0 24 24" fill="#fff"><path d="M6.6 10.8a15 15 0 0 0 6.6 6.6l2.2-2.2c.3-.3.7-.4 1-.2 1.1.4 2.3.6 3.6.6.6 0 1 .4 1 1V20c0 .6-.4 1-1 1A17 17 0 0 1 3 4c0-.6.4-1 1-1h3.5c.6 0 1 .4 1 1 0 1.3.2 2.5.6 3.6.1.3 0 .7-.2 1z"/></svg>
      +1 603 555 01 42
    </span>
    <span class="topbar-item">
      <svg width="13" height="10" viewBox="0 0 26 20" fill="#fff"><rect width="26" height="20" rx="2"/><path d="M1 2l12 9 12-9" stroke="#5aa8ea" stroke-width="2" fill="none"/></svg>
      info@brightharbormed.com
    </span>
    <span class="appointment-btn">Make an appointment</span>
    <svg width="13" height="13" viewBox="0 0 24 24" fill="none" stroke="#fff" stroke-width="3"><circle cx="10" cy="10" r="7"/><path d="M15 15l7 7"/></svg>
  </div>

  <header class="header">
    <div class="brand">
      <div class="brand-mark"></div>
      <span class="brand-name">Bright Harbor Medical Services</span>
    </div>
    <ul class="nav">
      <li class="is-active">Home</li>
      <li>About Us</li>
      <li>Our Services</li>
      <li>Team</li>
      <li>Blog</li>
      <li>Shop</li>
      <li>Contact Us</li>
    </ul>
  </header>

  <div class="hero-photo" role="img" aria-label="Photo of a smiling older couple sitting together on a sofa in a bright room"></div>

  <section class="intro">
    <h1 class="intro-title">Bright Harbor Medical Services, LLC</h1>
    <p class="intro-text">Advanced Care Planning helps your voice to always be heard. None of us like to think about getting sick, injured, or even dying but.. unfortunately wishful thinking doesn't protect us, but making a plane can help. We are here to help you arieve the peace of mind that comes from taking charge!</p>
  </section>

  <h2 class="services-heading">Our <span>Services</span></h2>
  <div class="divider"></div>
</div>
</body>
</html>
```